Tovel & Associates - London New Letting and Property Management Company *

Tovel & Associates LTD is a new company based in London, and works with brand new residential property in the city centre.

We are aiming to have 1000 new properties a year.

We are looking for something modern and minimalistic :
Logo ,Monogram, Paper Head and Business Card.

Target Market(s)

Internation landlords

Industry/Entity Type

Real Estate

Logo Text

Tovel & Associates

Colors

Designer to choose colors to be used in the design.

Requirements
Nice to have
• A particular monogram with "TA"
Should not have
• Little House over the logo

```html
<!DOCTYPE html>
<html lang="en">
<head>
<meta charset="utf-8">
<title>Tovel &amp; Associates – Business Card</title>
<link rel="stylesheet" href="https://fonts.googleapis.com/css2?family=Montserrat:wght@500;600&family=Mulish:wght@400;500&display=swap">
<style>
  :root {
    --backdrop: #2b2b2b;
    --paper: #ffffff;
    --navy: #17538a;
    --bright: #1d93d6;
    --ink: #555a5f;
    --rule: #1f5a8f;
  }
  * { margin: 0; padding: 0; box-sizing: border-box; }
  html, body { width: 1200px; height: 897px; overflow: hidden; }
  body {
    background: var(--backdrop);
    position: relative;
    font-family: "Mulish", sans-serif;
  }
  .card {
    position: absolute;
    left: 303px;
    width: 595px;
    height: 338px;
    box-shadow: 0 6px 18px rgba(0,0,0,0.45);
  }
  .card-front { top: 92px; background: var(--paper); }
  .card-back { top: 469px; background: var(--navy); }

  .brand-name {
    position: absolute;
    font-family: "Montserrat", sans-serif;
    font-weight: 600;
    text-align: center;
    line-height: 1.15;
    letter-spacing: 0.2px;
  }
  .card-front .brand-name {
    left: 300px; width: 280px; top: 92px;
    font-size: 25px; color: var(--navy);
  }
  .card-back .brand-name {
    left: 0; width: 595px; top: 172px;
    font-size: 36px; color: #ffffff;
  }

  .holder {
    position: absolute; left: 27px; top: 133px;
  }
  .holder-name {
    font-family: "Montserrat", sans-serif;
    font-weight: 600; font-size: 21px;
    color: var(--bright); letter-spacing: 0.2px;
    line-height: 1.1;
  }
  .holder-role {
    font-size: 15px; color: var(--ink); margin-top: 3px;
  }
  .divider {
    position: absolute; left: 27px; top: 192px;
    width: 537px; height: 2px; background: var(--rule);
  }
  .contacts {
    position: absolute; left: 27px; top: 205px;
    list-style: none; font-size: 15px; color: var(--ink);
  }
  .contacts li {
    display: flex; align-items: center; height: 20px;
  }
  .contacts svg { width: 12px; height: 12px; margin-right: 9px; flex: none; }
  .address {
    position: absolute; left: 27px; top: 274px;
    font-size: 15px; color: var(--ink); line-height: 21px;
    font-style: normal;
  }
  .website {
    position: absolute; right: 31px; top: 295px;
    font-size: 15px; color: var(--ink);
  }
  .accent-bar {
    position: absolute; left: 380px; bottom: 0;
    width: 187px; height: 9px; background: var(--bright);
  }
</style>
</head>
<body>
  <section class="card card-front" aria-label="Business card front">
    <div class="brand-name">Tovel &amp; Associates<br>LTD</div>

    <div class="holder">
      <p class="holder-name">ELENA VARGA</p>
      <p class="holder-role">Founder</p>
    </div>
    <div class="divider"></div>

    <ul class="contacts">
      <li>
        <svg viewBox="0 0 12 12" aria-hidden="true"><rect x="3" y="0.8" width="6" height="10.4" rx="1" fill="none" stroke="var(--bright)" stroke-width="1.4"/><line x1="5" y1="9" x2="7" y2="9" stroke="var(--bright)" stroke-width="1.2"/></svg>
        020. 555. 0142
      </li>
      <li>
        <svg viewBox="0 0 12 12" aria-hidden="true"><path d="M3 1.2 L5 3.5 L4 5 Q5 7.5 7 8.2 L8.5 7 L10.8 9 L9.5 10.8 Q4 10 1.5 3 Z" fill="var(--bright)"/></svg>
        020. 555. 0198
      </li>
      <li>
        <svg viewBox="0 0 12 12" aria-hidden="true"><rect x="1" y="2.5" width="10" height="7" fill="none" stroke="var(--bright)" stroke-width="1.3"/><path d="M1 2.8 L6 6.6 L11 2.8" fill="none" stroke="var(--bright)" stroke-width="1.3"/></svg>
        info@tovelassociates.co.uk
      </li>
    </ul>

    <address class="address">48 Harrow Lane Court<br>Kensington, London W8 4QT</address>
    <p class="website">www.tovelassociates.co.uk</p>
    <div class="accent-bar"></div>
  </section>

  <section class="card card-back" aria-label="Business card back">
    <div class="brand-name">Tovel &amp; Associates<br>LTD</div>
  </section>
</body>
</html>
```